Stationery Design Project

I need a stationary design for our company. we are based in Houston, TX and we are called Mira Vell Lending. And we are wanting to brand our MoneyMendPlus program, which includes our tax preparation and restoration, credit repair service. Although our business offers other programs, we are interested in mainly focusing on The MoneyMendPlus program. We are looking for way to brand our ourselves and I believe that a great stationery design will help in achieving this goal. Our logo design is blue and light blue. the slogan is orange.

Industry/Entity Type

Business

Requirements
Must have
• Address: 30871 Calloway Ln. B-22
Houston, TX 75419
Tel. 555-318-6207
Fax 555-294-7153
www.miravelllending.example
info@miravelllending.example
Our Slogan: Happiness, Restored!

```html
<!DOCTYPE html>
<html lang="en">
<head>
<meta charset="utf-8">
<title>MoneyMendPlus – Business Card</title>
<link rel="stylesheet" href="https://fonts.googleapis.com/css2?family=Questrial&family=Tinos&display=swap">
<style>
  :root {
    --backdrop: #e9e6e2;
    --card: #ffffff;
    --brand-blue: #1d6fa8;
    --navy: #123d66;
    --pale-frame: #c9d9e8;
    --slogan-orange: #f0901e;
    --ink: #222222;
    --ghost: #f1f3f6;
  }
  * { box-sizing: border-box; margin: 0; padding: 0; }
  html, body { width: 1200px; height: 714px; overflow: hidden; }
  body {
    background: var(--backdrop);
    position: relative;
    font-family: "Questrial", Arial, sans-serif;
    color: var(--ink);
  }
  .card {
    position: absolute;
    width: 540px;
    height: 310px;
    background: var(--card);
    box-shadow: 0 4px 14px rgba(0,0,0,0.18);
  }
  .card-front { left: 40px; top: 150px; }
  .card-back { left: 620px; top: 254px; }

  /* front */
  .brand-name {
    position: absolute;
    font-family: "Questrial", Arial, sans-serif;
    color: var(--brand-blue);
  }
  .card-front .brand-name { left: 40px; top: 62px; font-size: 40px; }
  .address {
    position: absolute; left: 40px; top: 140px;
    font-size: 14px; line-height: 18px;
  }
  .contact-list {
    position: absolute; left: 40px; top: 196px;
    list-style: none; font-size: 14px; line-height: 20px;
  }
  .contact-list li { display: flex; align-items: center; gap: 8px; }
  .contact-list svg { width: 12px; height: 12px; fill: var(--ink); flex: none; }
  .slogan {
    position: absolute; right: 40px; top: 48px; width: 170px;
    font-family: "Tinos", "Times New Roman", serif;
    font-size: 24px; line-height: 30px; text-align: center;
    color: var(--slogan-orange); letter-spacing: 0.5px;
  }
  .partner-square {
    position: absolute; right: 58px; top: 150px;
    width: 130px; height: 120px;
    background: var(--navy);
    border: 4px solid var(--pale-frame);
    display: flex; align-items: flex-end; justify-content: center;
    padding-bottom: 20px;
  }
  .partner-square span {
    font-family: "Tinos", "Times New Roman", serif;
    font-size: 13px; color: #ffffff;
  }

  /* back */
  .ghost-square {
    position: absolute; left: 170px; top: 28px;
    width: 230px; height: 250px; background: var(--ghost);
  }
  .card-back .brand-name {
    left: 0; right: 0; top: 108px; text-align: center; font-size: 58px;
  }
  .web-address {
    position: absolute; left: 0; right: 0; top: 214px; text-align: center;
    font-family: "Tinos", "Times New Roman", serif;
    font-size: 14px; letter-spacing: 5px; color: var(--ink);
  }
</style>
</head>
<body>

<section class="card card-front">
  <div class="brand-name">MoneyMendPlus</div>
  <address class="address" style="font-style:normal">30871 Calloway Ln. B-22<br>Houston, TX 75419</address>
  <ul class="contact-list">
    <li><svg viewBox="0 0 12 12" aria-hidden="true"><path d="M2.5 1 4.5 3 3.6 4.6c.7 1.5 2.3 3.1 3.8 3.8L9 7.5 11 9.5 9.6 11C5.3 10.7 1.3 6.7 1 2.4Z"/></svg>555-318-6207</li>
    <li><svg viewBox="0 0 12 12" aria-hidden="true"><path d="M3 1h6v3H3ZM1 5h10v5H9v1H3v-1H1Zm3 3v2h4V8Z"/></svg>555-294-7153</li>
    <li><svg viewBox="0 0 12 12" aria-hidden="true"><path d="M1 3h10v7H1Zm1 .8 4 3 4-3"/></svg>info@miravelllending.example</li>
    <li><svg viewBox="0 0 12 12" aria-hidden="true"><path d="M6 1a5 5 0 1 0 0 10A5 5 0 0 0 6 1Zm0 1.2c.8.8 1.3 2.2 1.4 3.2H4.6C4.7 4.4 5.2 3 6 2.2ZM2.3 6.6h2.3c.1 1.2.5 2.3 1 3.1A3.8 3.8 0 0 1 2.3 6.6Zm4.1 3.1c.5-.8.9-1.9 1-3.1h2.3a3.8 3.8 0 0 1-3.3 3.1Z"/></svg>www.miravelllending.example</li>
  </ul>
  <p class="slogan">HAPPINESS RESTORED!</p>
  <div class="partner-square"><span>Mira Vell Lending</span></div>
</section>

<section class="card card-back">
  <div class="ghost-square" aria-hidden="true"></div>
  <div class="brand-name">MoneyMendPlus</div>
  <p class="web-address">www.miravelllending.example</p>
</section>

</body>
</html>
```